13 Varno - new website design project

Our company Varno Electrical is developing a new lead generation website focused on Electrical, LED Lighting and Solar Power. We need a high converting website.

Example of our current website is www.varnoelectrical-example.com.au You can take content from this website for this new design. Our colours are red, black and white. For our new website we would like to promote Varno, Spark Every Day. Please listen to the jingle.

The below link is the company jingle that we have developed.
http://www.tunecraftdemo.com.au/vrn-tc-v1/

The key for this brief is to generate leads for Electrical, LED Lighting (for commercial) and Solar Power & Storage.

Target Market(s)

Business owners in Melbourne Victoria

Number of Pages Required

4 page

Colors
ec1f27
ffffff

Requirements
Must have
• This page must be clean, be in line with company branding and a high converting lead website.

```html
<!DOCTYPE html>
<html lang="en">
<head>
<meta charset="utf-8">
<title>Varno Electrical</title>
<link href="https://fonts.googleapis.com/css2?family=Nunito+Sans:wght@300;400;600;700&family=Open+Sans:wght@400;600;700&display=swap" rel="stylesheet">
<style>
:root{
  --red:#ec1f27;
  --red-dark:#c8151c;
  --ink:#222;
  --text:#555;
  --muted:#8a8a8a;
  --light:#f2f2f2;
  --line:#dcdcdc;
  --white:#fff;
  --sky-top:#6ea3df;
  --sky-bottom:#d9e8f7;
}
*{box-sizing:border-box;margin:0;padding:0}
html,body{width:1200px;height:3564px;overflow:hidden}
body{position:relative;background:var(--white);font-family:"Nunito Sans",sans-serif;color:var(--text)}
.abs{position:absolute}

/* header */
.site-header{position:absolute;left:0;top:0;width:1200px;height:105px;background:var(--white);box-shadow:0 2px 6px rgba(0,0,0,.08);z-index:2}
.brand{position:absolute;left:148px;top:22px;display:flex;flex-direction:column;align-items:flex-start}
.brand-name{display:flex;align-items:center;gap:8px;font-family:"Nunito Sans",sans-serif;font-weight:700;font-size:36px;color:var(--ink);line-height:1}
.brand-mark{width:16px;height:16px;background:var(--red);border-radius:50%}
.brand-tag{font-family:"Nunito Sans",sans-serif;font-weight:600;font-size:12px;color:var(--ink);margin-top:6px}
.main-nav{position:absolute;left:368px;top:46px;display:flex;gap:28px;font-family:"Open Sans",sans-serif;font-size:15px;color:var(--ink);letter-spacing:.2px}

/* hero */
.hero{position:absolute;left:0;top:105px;width:1200px;height:508px;background:linear-gradient(180deg,var(--sky-top),var(--sky-bottom))}
.hero-art{position:absolute;left:510px;top:20px;width:620px;height:470px;border-radius:50%;background:radial-gradient(circle at 50% 50%,#3d8a3a 0,#2f79c9 45%,rgba(255,255,255,.7) 70%,rgba(255,255,255,0) 72%)}
.hero-title{position:absolute;left:147px;top:258px;width:520px;font-weight:600;font-size:32px;line-height:45px;color:var(--white)}
.hero-dots{position:absolute;left:150px;top:402px;display:flex;gap:8px}
.hero-dots span{width:13px;height:13px;border-radius:50%;background:var(--white)}
.hero-dots span:first-child{background:transparent;border:2px solid var(--white)}

/* service cards */
.service-card{position:absolute;top:577px;width:302px;height:297px;background:var(--white);box-shadow:0 1px 5px rgba(0,0,0,.2)}
.service-photo{height:178px}
.service-card h3{margin-top:20px;text-align:center;font-weight:400;font-size:22px;color:var(--ink);letter-spacing:.5px}
.service-card p{margin:6px auto 0;width:240px;text-align:center;font-size:12px;line-height:16px;color:var(--muted)}
.btn-red{position:absolute;left:50%;bottom:-19px;transform:translateX(-50%);width:140px;height:38px;line-height:38px;text-align:center;background:var(--red);color:var(--white);font-family:"Open Sans",sans-serif;font-weight:600;font-size:13px;clip-path:polygon(10% 0,90% 0,100% 50%,90% 100%,10% 100%,0 50%)}

/* about */
.about{position:absolute;left:0;top:946px;width:1200px;height:456px;background:linear-gradient(90deg,#fff 0,#ececec 45%,#e4e4e4 100%)}
.about-photo{position:absolute;left:90px;top:70px;width:420px;height:300px;border-radius:40%;background:radial-gradient(ellipse at center,#5a5a5a 0,#8c8c8c 45%,rgba(236,236,236,0) 72%)}
.about h2{position:absolute;left:594px;top:92px;font-weight:400;font-size:34px;color:var(--ink)}
.about p{position:absolute;left:594px;top:152px;width:460px;font-size:14px;line-height:27px;color:var(--muted)}
.btn-outline{position:absolute;left:594px;top:314px;width:137px;height:38px;line-height:36px;text-align:center;border:2px solid var(--ink);font-family:"Open Sans",sans-serif;font-weight:600;font-size:13px;color:var(--ink)}

/* why choose */
.why-label{position:absolute;left:460px;top:1449px;width:280px;height:48px}
.why-label span{position:absolute;inset:0;display:flex;align-items:center;justify-content:center;font-size:24px;color:var(--white)}
.feature{position:absolute;width:460px}
.feature .num{position:absolute;left:0;top:-6px;font-size:70px;font-weight:300;color:#c8c8c8;line-height:1}
.feature h4{position:absolute;left:46px;top:4px;font-weight:400;font-size:22px;color:var(--ink)}
.feature p{position:absolute;left:46px;top:40px;width:420px;font-size:14px;line-height:22px;color:var(--muted)}
.icon{position:absolute}

/* clients */
.clients{position:absolute;left:0;top:2519px;width:1200px;height:316px;background:var(--light)}
.clients h2{position:absolute;width:100%;top:70px;text-align:center;font-weight:400;font-size:32px;color:#4a4a4a}
.client{position:absolute;top:137px;height:100px;display:flex;align-items:center;justify-content:center;font-weight:700;font-size:21px}
.notch{position:absolute;left:570px;top:2512px;width:0;height:0;border-left:14px solid transparent;border-right:14px solid transparent;border-top:14px solid var(--white);z-index:1}

/* testimonials */
.testimonials{position:absolute;left:0;top:2835px;width:1200px;height:365px;background:var(--red);color:var(--white)}
.testimonials h2{position:absolute;width:100%;top:56px;text-align:center;font-weight:600;font-size:24px;letter-spacing:.5px}
.testi-photo{position:absolute;left:271px;top:76px;width:180px;height:180px;border-radius:50%;border:6px solid var(--white);background:linear-gradient(180deg,#9aa3ad,#4d545c)}
.testi-quote{position:absolute;left:470px;top:118px;width:500px;font-size:20px;line-height:30px}
.testi-name{position:absolute;left:474px;top:221px;font-size:22px}
.testi-place{position:absolute;left:474px;top:254px;font-size:14px}
.arrow{position:absolute;top:140px}

/* footer */
.site-footer{position:absolute;left:0;top:3200px;width:1200px;height:364px;background:var(--white)}
.footer-brand{position:absolute;left:166px;top:112px}
.footer-brand .brand-name{font-size:46px}
.footer-brand .brand-tag{font-size:15px}
.footer-col{position:absolute;top:68px}
.footer-col h5{font-weight:400;font-size:18px;color:var(--red);margin-bottom:14px}
.footer-col li{list-style:none;font-size:13px;line-height:30px;color:#666}
.contact-line{font-size:13px;line-height:22px;color:#666}
.socials{display:flex;gap:8px;margin-top:12px}
.socials span{width:28px;height:28px;border-radius:50%}
.footer-rule{position:absolute;left:160px;top:297px;width:914px;height:1px;background:var(--line)}
.copyright{position:absolute;width:100%;top:320px;text-align:center;font-size:12px;color:#777}
</style>
</head>
<body>

<header class="site-header">
  <div class="brand">
    <div class="brand-name"><span class="brand-mark"></span>VARNO</div>
    <div class="brand-tag">Spark Every Day</div>
  </div>
  <nav class="main-nav">
    <span>VARNO STORY</span><span>OUR WORK</span><span>ELECTRICAL</span><span>LED LIGHTING</span><span>SOLAR POWER</span><span>CONTACT</span>
  </nav>
</header>

<section class="hero">
  <div class="hero-art" role="img" aria-label="Earth globe among clouds with solar panels and wind turbines"></div>
  <h1 class="hero-title">Australia's Largest fully Integrated Electrical &amp; Energy Solutions Provider</h1>
  <div class="hero-dots"><span></span><span></span><span></span><span></span></div>
</section>

<article class="service-card" style="left:140px">
  <div class="service-photo" role="img" aria-label="Electrician working on a switchboard" style="background:linear-gradient(135deg,#8aa0b4,#c9b48a 55%,#6b7a88)"></div>
  <h3>ELECTRICAL</h3>
  <p>In ullamcorper est eget tempor cursus neque mi consectetuer mi</p>
  <a class="btn-red">LEARN MORE</a>
</article>
<article class="service-card" style="left:451px">
  <div class="service-photo" role="img" aria-label="Building lit with green LED lighting at dusk" style="background:linear-gradient(180deg,#2b2f6e,#3a8f4a 60%,#c59a4a)"></div>
  <h3>LED LIGHTING</h3>
  <p>In ullamcorper est eget tempor cursus neque mi consectetuer mi</p>
  <a class="btn-red">LEARN MORE</a>
</article>
<article class="service-card" style="left:763px">
  <div class="service-photo" role="img" aria-label="Rows of solar panels under a blue sky" style="background:linear-gradient(180deg,#6fa5d8,#2c4f86 55%,#1f3a66)"></div>
  <h3>SOLAR POWER</h3>
  <p>In ullamcorper est eget tempor cursus neque mi consectetuer mi</p>
  <a class="btn-red">LEARN MORE</a>
</article>

<section class="about">
  <div class="about-photo" role="img" aria-label="Two LED spotlight bulbs"></div>
  <h2>About Varno Electrical</h2>
  <p>Varno Electrical was formed to be an expert Electricity Contracting Company providing services to all Residential and Commercial Customers. With over 10 years of experience, Varno Electrical has developed a highly-experienced team of professionals that ensure all our customer expectations are met.</p>
  <a class="btn-outline">READ MORE</a>
</section>

<div class="why-label">
  <svg width="280" height="48" viewBox="0 0 280 48"><polygon points="14,0 266,0 280,24 266,48 14,48 0,24" fill="#2b2b2b"/><polygon points="18,4 262,4 274,24 262,44 18,44 6,24" fill="none" stroke="#fff" stroke-width="1"/><line x1="30" y1="24" x2="50" y2="24" stroke="#fff" stroke-width="2"/><polyline points="44,19 50,24 44,29" fill="none" stroke="#fff" stroke-width="2"/><line x1="230" y1="24" x2="250" y2="24" stroke="#fff" stroke-width="2"/><polyline points="236,19 230,24 236,29" fill="none" stroke="#fff" stroke-width="2"/></svg>
  <span>Why Choose Us</span>
</div>

<div class="feature" style="left:154px;top:1565px">
  <span class="num">1</span><h4>Professional Service</h4>
  <p>When you hire a Varno Electrical Electrician you will get a professional and well-presented Electrician that comes skilled and ready to do the job.</p>
</div>
<svg class="icon" style="left:670px;top:1555px" width="150" height="150" viewBox="0 0 150 150" fill="none" stroke="#222" stroke-width="3"><rect x="60" y="10" width="80" height="50" rx="3"/><polyline points="72,60 72,76 88,60"/><line x1="74" y1="26" x2="126" y2="26"/><line x1="74" y1="36" x2="126" y2="36"/><line x1="74" y1="46" x2="110" y2="46"/><path d="M20 140 v-20 q0-24 30-26 q30 2 30 26 v20"/></svg>

<svg class="icon" style="left:300px;top:1755px" width="150" height="125" viewBox="0 0 150 125" fill="none" stroke="#ec1f27" stroke-width="3"><rect x="5" y="5" width="140" height="115" rx="4"/><line x1="5" y1="22" x2="145" y2="22"/><circle cx="75" cy="62" r="20"/><circle cx="75" cy="62" r="11"/><polyline points="62,78 58,104 75,94 92,104 88,78"/></svg>
<div class="feature" style="left:589px;top:1780px">
  <span class="num">2</span><h4>5 year Workmanship Guarantee</h4>
  <p>When you hire a Varno Electrical Electrician you will get a professional and well-presented Electrician that comes skilled and ready to do the job.</p>
</div>

<div class="feature" style="left:154px;top:1948px">
  <span class="num">3</span><h4>Value for Money</h4>
  <p>We provide extremely competitive pricing, which means you get value for money on quality that is comparable to the best in the industry.</p>
</div>
<svg class="icon" style="left:695px;top:1915px" width="150" height="130" viewBox="0 0 150 130" fill="none" stroke="#ec1f27" stroke-width="3"><circle cx="78" cy="30" r="25"/><path d="M86 20 q-8-6-14 0 q-4 6 6 10 q10 4 6 10 q-6 6-14 0"/><line x1="78" y1="12" x2="78" y2="48"/><path d="M5 90 h25 q20 0 30 10 h35 q8 0 8 8 h-40"/><path d="M30 118 h60 l50-30 q-8-10-20-4 l-30 16"/></svg>

<svg class="icon" style="left:385px;top:2135px" width="90" height="140" viewBox="0 0 90 140" fill="none" stroke="#222" stroke-width="3"><path d="M45 5 a38 38 0 0 0-22 69 v22 h44 v-22 a38 38 0 0 0-22-69z"/><line x1="28" y1="108" x2="62" y2="108"/><line x1="32" y1="118" x2="58" y2="118"/><path d="M45 90 v-40 q-18 0-18-18 q18 0 18 18 q0-20 20-20 q0 20-20 20"/></svg>
<div class="feature" style="left:589px;top:2156px">
  <span class="num">4</span><h4>Environmentally Friendly</h4>
  <p>We a committed to reducing carbon emissions by installing Solar Power and upgrading sites to LED Lighting. In addition to reducing the carbon emissions we recycle Fluorescent Tubes, Highbay Globes, Metal and Cardboard.</p>
</div>

<div class="feature" style="left:154px;top:2346px">
  <span class="num">5</span><h4>Fully Insured</h4>
  <p>Varno Electrical is fully insured and equipped to handle break downs and service call outs.</p>
</div>
<svg class="icon" style="left:668px;top:2320px" width="140" height="130" viewBox="0 0 140 130" fill="none" stroke="#ec1f27" stroke-width="3"><path d="M70 10 l34 12 v26 q0 30-34 46 q-34-16-34-46 v-26z"/><path d="M70 24 l22 8 v16 q0 20-22 32"/><path d="M10 40 v50 q0 16 16 26 l20 10"/><path d="M130 40 v50 q0 16-16 26 l-20 10"/></svg>

<div class="notch"></div>
<section class="clients">
  <h2>Our Satisfied Clients</h2>
  <div class="client" style="left:204px;width:160px;color:#c2202a;font-weight:400;font-size:30px">Velvetline</div>
  <div class="client" style="left:409px;width:173px;background:#f7e600;color:#111">Outback Supply Co</div>
  <div class="client" style="left:618px;width:173px;background:#e0262b;color:#fff;font-size:19px">Heron Plumbing</div>
  <div class="client" style="left:827px;width:173px;background:#d6261e;color:#f6c400">Goldbun Burgers</div>
</section>

<section class="testimonials">
  <h2>TESTIMONIALS</h2>
  <svg class="arrow" style="left:152px" width="26" height="56" viewBox="0 0 26 56"><polyline points="24,2 2,28 24,54" fill="none" stroke="#fff" stroke-width="2" opacity=".7"/></svg>
  <svg class="arrow" style="left:1012px" width="26" height="56" viewBox="0 0 26 56"><polyline points="2,2 24,28 2,54" fill="none" stroke="#fff" stroke-width="2" opacity=".7"/></svg>
  <div class="testi-photo" role="img" aria-label="Interior of a warehouse with new lighting installed"></div>
  <p class="testi-quote"><b style="font-size:36px">“</b> Excellent work and very professional. Marcus takes time to explain everything and demonstrate workings. Very clear precise and accurate <b style="font-size:36px">”</b></p>
  <div class="testi-name">Delmar</div>
  <div class="testi-place">Cranbourne North VIC</div>
</section>

<footer class="site-footer">
  <div class="brand footer-brand" style="left:166px;top:112px">
    <div class="brand-name"><span class="brand-mark"></span>VARNO</div>
    <div class="brand-tag">Spark Every Day</div>
  </div>
  <div class="footer-col" style="left:432px">
    <h5>COMPANY</h5>
    <ul><li>Home</li><li>About Us</li><li>Our Work</li><li>Term of Use</li><li>Contact Us</li></ul>
  </div>
  <div class="footer-col" style="left:634px">
    <h5>RESOURCES</h5>
    <ul><li>Led Lighting</li><li>Solar Power</li><li>Electrical</li><li>Career</li><li>Privacy</li></ul>
  </div>
  <div class="footer-col" style="left:834px">
    <h5>CONTACT US</h5>
    <p class="contact-line">214 Harbour Lane Suite 12<br>Dandenong, VIC 3175</p>
    <p class="contact-line" style="margin-top:10px">(03) 9000 0000<br>info@varnoelectrical-example.com.au</p>
    <div class="socials"><span style="background:#3fa9e0"></span><span style="background:#3b5a9a"></span><span style="background:#0e76a8"></span><span style="background:#dd4b39"></span></div>
  </div>
  <div class="footer-rule"></div>
  <p class="copyright">© 2017 Company Name  All right reserved</p>
</footer>

</body>
</html>
```